We need a home page design only (no coding necessary) for a motorcycle dealer. He wants the theme to be Modern-Industrial with vintage details. Please read the requirements below.

Client likes http://www.pelicanbaymotorworks.example/ and wants a similar layout.

Dealer info:
Lone Ridge Cycle Depot (logo attached)
210.555.0187
384 W Calloway Ln Ste 207
San Antonio, TX 78299
Hours
Sun-Mon: Closed
Tue-Sat: 9a – 6p

Slideshow images - I've attached a few so you can see his inventory, it may help with the design

Call-to-action buttons:
Financing
Sell Your Bike
View Inventory

Theme: Modern-Industrial with Vintage details
Main background: Artistic or vintage image of motorcycle (see link for examples from client: http://instagram.com/copperandgale#)
Content background: likes the use of 'black wood' on http://www.pelicanbaymotorworks.example - find a way to incorporate the wood background somewhere on the design

Accent Colors: Black, white and pops of red
Featured Vehicles location: Middle (in between the call-to-action buttons and the verbiage)
Social Networking: Facebook, Instagram

Client likes http://www.pelicanbaymotorworks.example/ and wants a similar layout:
-wants the navigation bar above the banner/header
-wants the logo centered in the banner/header (open to the placement of the phone number, address and social media icons, as long as they show in the banner)
-wants to leave gaps between the sections so the background is visible

Attachments:
-layout that the client provided (LRCD_HOME_PAGE)
-logo (LRCD_BLACK & LRCD_W)
-psd file showing the typical layout used (sample-site) - ONLY A SUGGESTION!
-a few slideshow images to show client's inventory (the rest of the files)

Please let me know if you have any questions and thank you in advance for your work.

Thank you all for your wonderful mockups. I've sent them to the client and am awaiting the response. I will keep you all updated. Best regards, Marjorie

Thank you all, I am just waiting for feedback from the client. I will post the feedback as soon as I get a response from the client. Best regards, Marjorie

```html
<!DOCTYPE html>
<html lang="en">
<head>
<meta charset="utf-8">
<title>Lone Ridge Cycle Depot — Home</title>
<link href="https://fonts.googleapis.com/css2?family=Roboto+Condensed:wght@400;700&family=Roboto:wght@400&display=swap" rel="stylesheet">
<style>
  :root {
    --red: #a9160f;
    --red-bright: #d8251b;
    --red-deep: #8a110b;
    --black: #0b0b0b;
    --panel: rgba(8,8,8,0.93);
    --white: #ffffff;
    --muted: #8e8e8e;
    --footer: #101010;
    --head: "Roboto Condensed", Arial, sans-serif;
    --body: "Roboto", Arial, sans-serif;
  }
  * { margin: 0; padding: 0; box-sizing: border-box; }
  html, body { width: 938px; height: 1200px; overflow: hidden; background: #1a1a1a; }
  .page { position: relative; width: 938px; height: 1200px; overflow: hidden; font-family: var(--body); color: var(--white); }
  .abs { position: absolute; }

  .backdrop { position: absolute; left: 0; top: 0; width: 938px; height: 925px;
    background:
      radial-gradient(circle at 930px 250px, rgba(150,30,22,0.55) 0, rgba(150,30,22,0) 40px),
      radial-gradient(circle at 300px 70px, rgba(150,30,22,0.45) 0, rgba(150,30,22,0) 30px),
      radial-gradient(ellipse at 72% 28%, #4a4a4a 0%, #2c2c2c 30%, #161616 70%),
      #141414; }

  .nav { left: 0; top: 0; width: 938px; height: 40px; background: var(--red); }
  .nav ul { list-style: none; position: absolute; left: 134px; top: 0; display: flex; height: 40px; }
  .nav li { font-family: var(--head); font-weight: 700; font-size: 10.5px; line-height: 42px; text-align: center; }
  .nav li.active { background: var(--red-deep); }
  .nav li a { color: var(--white); text-decoration: none; display: block; }

  .head-contact { left: 135px; top: 78px; font-family: var(--head); font-size: 8.5px; line-height: 16px; color: #cfcfcf; }
  .head-contact h4 { font-weight: 700; font-size: 11px; line-height: 14px; color: var(--white); margin-bottom: 4px; }
  .head-divider { left: 244px; top: 96px; width: 1px; height: 32px; background: #4a4a4a; }
  .head-phone { left: 257px; top: 107px; font-family: var(--head); font-size: 8.5px; color: #cfcfcf; display: flex; align-items: center; gap: 4px; }

  .logo { left: 370px; top: 55px; width: 184px; height: 95px; border: 3px solid #d6d6d6; border-radius: 14px;
    background: rgba(18,18,18,0.7); display: flex; align-items: center; justify-content: center; gap: 8px; }
  .logo .mark { width: 9px; height: 9px; background: #d6d6d6; }
  .logo span { font-family: var(--head); font-weight: 700; font-size: 15px; line-height: 17px; color: #e6e6e6; text-align: center; }

  .follow { left: 659px; top: 91px; display: flex; align-items: center; gap: 7px; font-family: var(--head); font-size: 9px; color: #b0b0b0; }
  .follow .dot { display: block; width: 22px; height: 22px; border-radius: 50%; background: var(--red-bright); }

  .slider { left: 134px; top: 162px; width: 670px; height: 316px; background: #3a3a3a; padding: 5px; }
  .slider .photo { width: 100%; height: 100%;
    background: linear-gradient(105deg, #d2cdc3 0%, #bdb8ae 30%, #3a3150 48%, #241e36 58%, #6f6f7c 75%, #d9d9d9 100%); }
  .slide-tag { left: 151px; top: 338px; background: var(--black); font-family: var(--head); font-weight: 700; font-size: 17px; line-height: 20px; padding: 11px 20px 10px; }
  .slide-title { left: 151px; top: 385px; background: var(--red); font-family: var(--head); font-weight: 700; font-size: 24px; line-height: 30px; padding: 5px 17px 7px; }
  .arrows { display: flex; gap: 2px; }
  .arrows span { width: 17px; height: 17px; background: var(--red-bright); display: flex; align-items: center; justify-content: center; }
  .slider-arrows { left: 752px; top: 448px; }

  .brands { left: 134px; top: 488px; width: 670px; height: 46px; background: #282828; border: 2px solid #383838;
    display: flex; align-items: center; justify-content: space-around; padding: 0 10px; }
  .brands i { display: block; height: 14px; background: #9a9a9a; border-radius: 3px; }
  .brands i.tall { height: 22px; border-radius: 4px; }

  .cta { top: 547px; width: 214px; height: 120px; text-decoration: none; color: var(--white); }
  .cta .photo { height: 91px; }
  .cta .label { height: 29px; background: var(--red); font-family: var(--head); font-weight: 700; font-size: 14px; line-height: 30px; padding-left: 11px; }

  .welcome-panel { left: 134px; top: 682px; width: 670px; height: 224px; background: var(--panel); }
  .contact-card { left: 154px; top: 705px; width: 175px; height: 179px; background: var(--red); padding: 22px 19px; font-family: var(--head); font-size: 8.5px; line-height: 16px; }
  .contact-card h3 { font-size: 16px; font-weight: 700; line-height: 18px; margin-bottom: 5px; }
  .contact-card .addr { padding-left: 1px; }
  .contact-card h5 { font-size: 10px; font-weight: 700; line-height: 14px; margin-top: 9px; margin-bottom: 3px; }
  .contact-card .phone { display: flex; align-items: center; gap: 6px; margin-top: 6px; }
  .welcome { left: 355px; top: 703px; width: 428px; }
  .welcome h2 { font-family: var(--head); font-weight: 700; font-size: 16px; line-height: 20px; }
  .welcome h1 { font-family: var(--head); font-weight: 700; font-size: 20px; line-height: 24px; color: #d02a20; margin-bottom: 7px; }
  .welcome p { font-family: Arial, sans-serif; font-size: 8px; line-height: 16px; color: var(--muted); margin-bottom: 16px; padding-left: 2px; }

  .wood { left: 0; top: 925px; width: 938px; height: 222px;
    background:
      repeating-linear-gradient(163deg, rgba(0,0,0,0) 0, rgba(0,0,0,0) 44px, rgba(0,0,0,0.55) 44px, rgba(0,0,0,0.55) 46px, rgba(255,255,255,0.05) 46px, rgba(255,255,255,0.05) 47px),
      repeating-linear-gradient(163deg, rgba(255,255,255,0.025) 0, rgba(255,255,255,0.025) 3px, rgba(0,0,0,0.04) 3px, rgba(0,0,0,0.04) 9px),
      radial-gradient(ellipse at 50% 40%, #383838 0%, #262626 55%, #1a1a1a 100%); }
  .featured-title { left: 134px; top: 955px; font-family: var(--head); font-weight: 700; font-size: 16px; line-height: 20px; }
  .featured-arrows { left: 765px; top: 956px; }
  .featured-arrows span { width: 18px; height: 18px; }
  .thumb { top: 992px; width: 122px; height: 115px; background: #111; padding: 4px; }
  .thumb .photo { width: 100%; height: 100%; }

  .footer { left: 0; top: 1147px; width: 938px; height: 53px; background: var(--footer); font-family: Arial, sans-serif; font-size: 8.5px; color: #9a9a9a; }
  .footer nav { position: absolute; left: 135px; top: 21px; display: flex; gap: 13px; }
  .footer .copy { position: absolute; left: 637px; top: 21px; }
</style>
</head>
<body>
<div class="page">
  <div class="backdrop" role="img" aria-label="Dark moody close-up photograph of a vintage motorcycle as page background"></div>

  <header class="abs nav">
    <ul>
      <li class="active" style="width:74px"><a>HOME</a></li>
      <li style="width:96px"><a>ABOUT US</a></li>
      <li style="width:79px"><a>VEHICLE</a></li>
      <li style="width:92px"><a>FINANCING</a></li>
      <li style="width:108px"><a>TESTIMONIALS</a></li>
      <li style="width:78px"><a>SERVICE</a></li>
      <li style="width:104px"><a>CONTACT US</a></li>
    </ul>
  </header>

  <div class="abs head-contact">
    <h4>CONTACT</h4>
    384 W CALLOWAY LN STE 207<br>SAN ANTONIO, TX 78299
  </div>
  <div class="abs head-divider"></div>
  <div class="abs head-phone">
    <svg width="6" height="10" viewBox="0 0 6 10"><rect x="0.5" y="0.5" width="5" height="9" rx="1" fill="none" stroke="#d0d0d0"/></svg>
    CALL US : 210.555.0187
  </div>

  <div class="abs logo"><i class="mark"></i><span>LONE RIDGE<br>CYCLE DEPOT</span></div>

  <div class="abs follow">FOLLOW US : <i class="dot"></i><i class="dot"></i></div>

  <section class="abs slider">
    <div class="photo" role="img" aria-label="Chrome and purple cruiser motorcycle parked by a garage door"></div>
  </section>
  <div class="abs slide-tag">MOTOR CYCLE DEALER IN TEXAS</div>
  <div class="abs slide-title">LONE RIDGE CYCLE DEPOT</div>
  <div class="abs arrows slider-arrows">
    <span><svg width="6" height="8"><path d="M5 0L1 4l4 4" stroke="#fff" fill="none"/></svg></span>
    <span><svg width="6" height="8"><path d="M1 0l4 4-4 4" stroke="#fff" fill="none"/></svg></span>
  </div>

  <div class="abs brands" aria-label="Partner brands">
    <i style="width:92px"></i><i class="tall" style="width:56px"></i><i style="width:74px"></i><i style="width:78px"></i><i style="width:82px"></i><i class="tall" style="width:50px"></i><i class="tall" style="width:62px"></i>
  </div>

  <a class="abs cta" style="left:134px">
    <div class="photo" role="img" aria-label="Chrome gauges and handlebars of a motorcycle" style="background:linear-gradient(160deg,#e9e6df,#9a9690 60%,#3a3550)"></div>
    <div class="label">FINANCING</div>
  </a>
  <a class="abs cta" style="left:362px">
    <div class="photo" role="img" aria-label="Airbrushed chrome motorcycle tank" style="background:linear-gradient(160deg,#d8d4cc,#8b8b8b 55%,#2c2c2c)"></div>
    <div class="label">SELL YOUR BIKE</div>
  </a>
  <a class="abs cta" style="left:590px">
    <div class="photo" role="img" aria-label="Red touring motorcycle dashboard" style="background:linear-gradient(160deg,#f0f0f0,#c22018 55%,#5a0b08)"></div>
    <div class="label">VIEW INVENTORY</div>
  </a>

  <section class="abs welcome-panel"></section>
  <aside class="abs contact-card">
    <h3>CONTACT</h3>
    <div class="addr">384 W CALLOWAY LN STE 207<br>SAN ANTONIO, TX 78299</div>
    <div class="phone">
      <svg width="10" height="16" viewBox="0 0 10 16"><rect x="1" y="1" width="8" height="14" rx="1" fill="none" stroke="#fff" stroke-width="1.5"/><line x1="3" y1="12.5" x2="7" y2="12.5" stroke="#fff"/></svg>
      CALL US : 210.555.0187
    </div>
    <h5>HOURS</h5>
    <div>SUN-MON: CLOSED<br>TUE-SAT: 9A – 6P</div>
  </aside>
  <div class="abs welcome">
    <h2>WELCOME TO</h2>
    <h1>LONE RIDGE CYCLE</h1>
    <p>It is a long established fact that a reader will be distracted by the readable content of a page when looking at its layout. The point of using Lorem Ipsum is that it has a more-or-less normal distribution of letters, as opposed to using 'Content here, content here', making it look like readable English. Many desktop publishing packages and web page editors now use Lorem Ipsum as their default model text, and a search for 'lorem ipsum' will uncover many web sites still in their infancy. Various versions have evolved over the years, sometimes by accident, sometimes on purpose.</p>
    <p>Many desktop publishing packages and web page editors now use Lorem Ipsum as their default model text, and a search for 'lorem ipsum' will uncover many web sites still in their infancy.</p>
  </div>

  <section class="abs wood" role="img" aria-label="Black wood plank background"></section>
  <h2 class="abs featured-title">FEATURED PRODUCTS</h2>
  <div class="abs arrows featured-arrows">
    <span><svg width="6" height="8"><path d="M5 0L1 4l4 4" stroke="#fff" fill="none"/></svg></span>
    <span><svg width="6" height="8"><path d="M1 0l4 4-4 4" stroke="#fff" fill="none"/></svg></span>
  </div>
  <div class="abs thumb" style="left:134px"><div class="photo" role="img" aria-label="Front view of black cruiser headlight" style="background:linear-gradient(160deg,#eee,#777 50%,#151515)"></div></div>
  <div class="abs thumb" style="left:270px"><div class="photo" role="img" aria-label="Airbrushed chrome tank" style="background:linear-gradient(160deg,#ddd,#8a8a8a 55%,#2a2a2a)"></div></div>
  <div class="abs thumb" style="left:406px"><div class="photo" role="img" aria-label="Purple cruiser gauges" style="background:linear-gradient(160deg,#e8e4da,#a8a49c 50%,#3a3356)"></div></div>
  <div class="abs thumb" style="left:544px"><div class="photo" role="img" aria-label="Red touring bike dashboard" style="background:linear-gradient(160deg,#b51c15,#d8261c 55%,#6a0c08)"></div></div>
  <div class="abs thumb" style="left:682px"><div class="photo" role="img" aria-label="Purple chrome cruiser side view" style="background:linear-gradient(160deg,#d6d3cb,#6c6c78 55%,#2b2440)"></div></div>

  <footer class="abs footer">
    <nav><span>Home</span><span>|</span><span>About Us</span><span>|</span><span>Vehicle</span><span>|</span><span>Financing</span><span>|</span><span>Testimonials</span><span>|</span><span>Service</span><span>|</span><span>Contact us</span></nav>
    <div class="copy">© 2014 Lone Ridge cycle. All rights reserved.</div>
  </footer>
</div>
</body>
</html>
```